We want to design total new business card and logo for Kestrel Building Services Ltd

Our company name Kestrel Building Services Ltd. Design new logo and business card , need hi-end luxury style art for architecture and construction industry. The card should simple but stylish. Our business focus on CONNECT tradesman to construction company, help marketing construction company tender oversea projects, managing franchise in construction sector, delivery amazing services to our client, so Logo should show the CONNECTION IDEA, CONNECTING PEOPLE, LUXURY. Visit our website for more information: kestrelgroup.example.nz

Target Market(s)

Directors or managers

Industry/Entity Type

Construction Company

Contact Information for Business Card

Name, Title, Mobile, Email, Website

Font styles to use
Serif

Colors

Designer to choose colors to be used in the design.

Requirements
Must have
• Simple and luxury, connection icon
Nice to have
• Special materials, plastic card, look through,...
• Look new ideas.

```html
<!DOCTYPE html>
<html lang="en">
<head>
<meta charset="utf-8">
<title>Kestrel Building Services – Business Card</title>
<link rel="stylesheet" href="https://fonts.googleapis.com/css2?family=Cormorant+Garamond:wght@600;700&family=Lora:wght@400;500&display=swap">
<style>
  :root {
    --backdrop: #2a2a2c;
    --card-top: #1c1c1e;
    --card-bottom: #0b0b0c;
    --accent: #16a9cc;
    --text-light: #e6e6e6;
    --divider: #4a4a4e;
  }
  * { box-sizing: border-box; margin: 0; padding: 0; }
  html, body {
    width: 1200px; height: 900px; overflow: hidden;
    background: var(--backdrop);
    font-family: "Lora", Georgia, serif;
  }
  .canvas {
    position: relative; width: 1200px; height: 900px;
    display: flex; flex-direction: column; align-items: center;
    justify-content: center; gap: 50px;
  }
  .card {
    position: relative; width: 600px; height: 340px;
    background: linear-gradient(160deg, var(--card-top), var(--card-bottom));
    box-shadow: 0 10px 30px rgba(0,0,0,.45);
    overflow: hidden;
  }
  .card__stripe {
    position: absolute; left: 0; right: 0; bottom: 0; height: 12px;
    background: var(--accent);
  }
  /* Front */
  .brand {
    position: absolute; left: 0; right: 0; top: 118px; text-align: center;
  }
  .brand__name {
    font-family: "Cormorant Garamond", Georgia, serif; font-weight: 700;
    font-size: 36px; letter-spacing: 1px; color: var(--accent);
    text-transform: uppercase; line-height: 1.1;
    display: inline-flex; align-items: center; gap: 12px;
  }
  .brand__mark {
    width: 12px; height: 12px; border-radius: 50%;
    background: var(--accent); display: inline-block;
  }
  .brand__tagline {
    margin-top: 10px; font-size: 14px; letter-spacing: 1.5px;
    color: var(--text-light); text-transform: uppercase;
  }
  /* Back */
  .person {
    position: absolute; left: 60px; top: 95px; width: 225px; text-align: right;
  }
  .person__name {
    font-family: "Cormorant Garamond", Georgia, serif; font-weight: 700;
    font-size: 23px; color: var(--accent); text-transform: uppercase; letter-spacing: 1px;
    line-height: 1.1;
  }
  .person__title { font-size: 15px; color: var(--text-light); margin-top: 4px; }
  .divider {
    position: absolute; left: 305px; top: 92px; width: 1px; height: 112px;
    background: var(--divider);
  }
  .contact {
    position: absolute; left: 322px; top: 100px; list-style: none;
    font-size: 15px; color: var(--text-light); line-height: 24px;
  }
  .contact li { display: flex; align-items: center; gap: 9px; }
  .contact svg { width: 13px; height: 13px; fill: var(--accent); flex: none; }
  .company {
    position: absolute; left: 0; right: 0; top: 246px; text-align: center;
  }
  .company__name {
    font-family: "Cormorant Garamond", Georgia, serif; font-weight: 700;
    font-size: 18px; letter-spacing: 1px; color: var(--accent); text-transform: uppercase;
  }
  .company__address { font-size: 15px; color: var(--text-light); }
</style>
</head>
<body>
<main class="canvas">
  <section class="card card--front" aria-label="Business card front">
    <div class="brand">
      <div class="brand__name"><span class="brand__mark"></span>Kestrel Building Services</div>
      <p class="brand__tagline">Connecting trades, projects &amp; people</p>
    </div>
    <div class="card__stripe"></div>
  </section>

  <section class="card card--back" aria-label="Business card back">
    <div class="person">
      <p class="person__name">Marcus Reid</p>
      <p class="person__title">Managing Director</p>
    </div>
    <div class="divider"></div>
    <ul class="contact">
      <li><svg viewBox="0 0 16 16"><path d="M3 1l3 3-2 2c1 2 4 5 6 6l2-2 3 3-2 2C7 15 1 9 1 3z"/></svg>0800 555 014</li>
      <li><svg viewBox="0 0 16 16"><path d="M3 1l3 3-2 2c1 2 4 5 6 6l2-2 3 3-2 2C7 15 1 9 1 3z"/></svg>021 555 0192</li>
      <li><svg viewBox="0 0 16 16"><path d="M1 3h14v10H1z M1 3l7 6 7-6" fill="none" stroke="#16a9cc" stroke-width="1.8"/></svg>info@kestrelgroup.example.nz</li>
      <li><svg viewBox="0 0 16 16"><circle cx="8" cy="8" r="7"/></svg>www.kestrelgroup.example.nz</li>
    </ul>
    <div class="company">
      <p class="company__name">Kestrel Building Services Ltd</p>
      <p class="company__address">12 Harbour Lane, Eastdale, Auckland 2090, New Zealand</p>
    </div>
    <div class="card__stripe"></div>
  </section>
</main>
</body>
</html>
```